A5, portrait
Theme is science
audience is VIPS, politicians, executives
this is a really important event, we want a very classy invitation
include logo for bloom and grow and lantern but lantern one bigger
images attached
Have attached some styles we like but doesn't need to be these colours. If we can incorporate some colours from our logo would be good but don't make too colourful and childish

You’re invited to the official opening and launch of Lantern, Centre of Discovery. an industry first, pioneering, STEM hub.

Saturday 30th April, 2022

10:00 am – 12:00 pm

42 Harlow Lane, Fernwood

Light canapes provided. Dress code is smart/casual

All guests will be given a guided walk through of Australia’s first dedicated STEM education hub for children aged 3-6.

Invitation only

RSVP: 18 April to marketing@bloomandgrow.edu.au

```html
<!DOCTYPE html>
<html lang="en">
<head>
<meta charset="utf-8">
<title>Lantern Opening Invitation</title>
<link rel="stylesheet" href="https://fonts.googleapis.com/css2?family=Cinzel:wght@400;500&family=Crimson+Text:ital,wght@0,400;0,700;1,400&display=swap">
<style>
  :root {
    --page: #d8d4ce;
    --ink-deep: #05040a;
    --violet-dark: #1c1838;
    --violet: #2b2552;
    --violet-mid: #3a3270;
    --glow: #7f72d8;
    --copper: #d8692a;
    --copper-soft: #b25a24;
    --white: #ffffff;
    --navy-text: #2a2550;
  }
  * { box-sizing: border-box; margin: 0; padding: 0; }
  html, body { width: 1200px; height: 900px; overflow: hidden; }
  body {
    background: var(--page);
    font-family: "Crimson Text", Georgia, serif;
    position: relative;
  }
  .invitation {
    position: absolute;
    left: 300px; top: 24px;
    width: 600px; height: 852px;
    background: linear-gradient(160deg, var(--ink-deep) 0%, var(--violet-dark) 22%, var(--violet) 55%, var(--violet) 100%);
    overflow: hidden;
    color: var(--white);
    box-shadow: 0 10px 30px rgba(0,0,0,.25);
  }
  .invitation__lower {
    position: absolute; left: 0; top: 619px; width: 600px; height: 193px;
    background: linear-gradient(120deg, var(--violet) 0%, var(--violet-dark) 55%, var(--ink-deep) 100%);
  }
  .frame-corner {
    position: absolute; left: 50px; top: 87px;
    width: 199px; height: 259px;
    border-top: 3px solid var(--copper-soft);
    border-left: 3px solid var(--copper-soft);
    -webkit-mask: linear-gradient(180deg, #000 60%, transparent 100%);
            mask: linear-gradient(180deg, #000 60%, transparent 100%);
  }
  .headline {
    position: absolute; left: 79px; top: 112px;
    font-family: "Cinzel", "Times New Roman", serif;
    color: var(--copper);
    font-weight: 400;
    line-height: 33px;
    font-size: 37px;
  }
  .headline__small { font-size: 29px; }
  .headline-rule {
    position: absolute; left: 225px; top: 172px;
    width: 179px; height: 1.5px;
    background: linear-gradient(90deg, var(--copper) 0%, var(--copper-soft) 70%, transparent 100%);
  }
  .intro {
    position: absolute; left: 79px; top: 186px; width: 400px;
    font-style: italic; font-size: 20.5px; line-height: 24px;
  }
  .details { position: absolute; left: 192px; top: 288px; list-style: none; }
  .details__item {
    display: flex; align-items: center;
    height: 30px; font-size: 21px;
  }
  .details__icon { width: 16px; height: 16px; margin-right: 17px; fill: var(--white); }
  .feature-image {
    position: absolute; left: 0; top: 397px; width: 600px; height: 222px;
    background:
      radial-gradient(circle at 300px 112px, #b9b0ff 0%, #6d5fd0 14%, transparent 30%),
      linear-gradient(90deg, #2a2566 0%, #4a3fa6 40%, #5e4fc0 65%, #2a2566 100%);
  }
  .notes {
    position: absolute; left: 79px; top: 640px; width: 440px;
    font-size: 15px; line-height: 24px;
  }
  .invite-only {
    position: absolute; left: 216px; top: 750px;
    width: 166px; height: 28px;
    border: 2px solid var(--copper-soft);
    color: var(--copper);
    font-size: 16px; line-height: 24px; text-align: center;
    letter-spacing: .2px;
  }
  .brand-lantern {
    position: absolute; left: 432px; top: 30px; width: 143px;
    text-align: center; color: var(--white);
    font-family: "Crimson Text", Georgia, serif; font-weight: 700;
  }
  .brand-lantern__mark {
    display: block; width: 44px; height: 44px; margin: 0 auto 6px;
    border-radius: 50%; background: var(--copper);
  }
  .brand-lantern__name { display: block; font-size: 34px; line-height: 34px; letter-spacing: 1px; }
  .brand-lantern__tag { display: block; font-size: 13px; line-height: 18px; }
  .brand-bloom {
    position: absolute; left: 465px; top: 744px; width: 110px;
    display: flex; flex-direction: column; align-items: center;
    color: var(--white); font-weight: 700; font-size: 14px; line-height: 16px; text-align: center;
  }
  .brand-bloom__mark { width: 22px; height: 22px; background: var(--copper); margin-bottom: 6px; }
  .rsvp {
    position: absolute; left: 0; top: 812px; width: 600px; height: 40px;
    background: var(--white); color: var(--navy-text);
    font-weight: 700; font-size: 19px; line-height: 40px; text-align: center;
  }
</style>
</head>
<body>
  <main class="invitation">
    <div class="invitation__lower"></div>

    <div class="brand-lantern">
      <span class="brand-lantern__mark"></span>
      <span class="brand-lantern__name">Lantern</span>
      <span class="brand-lantern__tag">Centre of Discovery</span>
    </div>

    <div class="frame-corner"></div>
    <h1 class="headline">Y<span class="headline__small">OU’RE</span><br>INVITED</h1>
    <div class="headline-rule"></div>

    <p class="intro">to the official opening and launch of Lantern, Centre of Discovery.&nbsp; An industry first, pioneering, STEM hub.</p>

    <ul class="details">
      <li class="details__item">
        <svg class="details__icon" viewBox="0 0 16 16" aria-hidden="true"><path d="M2 3h12v12H2z M3 6.5v7.5h10V6.5z" fill-rule="evenodd"/><rect x="4" y="1" width="2" height="4"/><rect x="10" y="1" width="2" height="4"/><rect x="4.5" y="8" width="2" height="2"/><rect x="7.5" y="8" width="2" height="2"/><rect x="10.5" y="8" width="2" height="2"/><rect x="4.5" y="11" width="2" height="2"/><rect x="7.5" y="11" width="2" height="2"/></svg>
        Saturday 30th April, 2022
      </li>
      <li class="details__item">
        <svg class="details__icon" viewBox="0 0 16 16" aria-hidden="true"><path d="M8 0a8 8 0 1 1 0 16A8 8 0 0 1 8 0zm-.9 3v5.6l3.8 2.6.9-1.3-3.2-2.2V3z"/></svg>
        10:00 am – 12:00 pm
      </li>
      <li class="details__item">
        <svg class="details__icon" viewBox="0 0 16 16" aria-hidden="true"><path d="M8 0a5.5 5.5 0 0 1 5.5 5.5C13.5 9.5 8 16 8 16S2.5 9.5 2.5 5.5A5.5 5.5 0 0 1 8 0zm0 3.3a2.2 2.2 0 1 0 0 4.4 2.2 2.2 0 0 0 0-4.4z"/></svg>
        42 Harlow Lane, Fernwood
      </li>
    </ul>

    <div class="feature-image" role="img" aria-label="Photo of a glowing plasma ball on a plinth inside the violet-lit STEM hub"></div>

    <p class="notes">Light canapes provided. Dress code is smart/casual<br>All guests will be given a guided walk through of Australia’s first dedicated STEM education hub for children aged 3-6.</p>

    <div class="invite-only">INVITATION ONLY</div>

    <div class="brand-bloom">
      <span class="brand-bloom__mark"></span>
      Bloom and Grow
    </div>

    <p class="rsvp">RSVP: 18 April to marketing@bloomandgrow.edu.au</p>
  </main>
</body>
</html>
```